Boutique town planning business needs a Business Card design

We need a business card design for a new company called Fernhill Civic Studio. We provide town planning and urban design services to government, business and community groups. We would like to see the designs use the colours in the logo (blue, deep red, green and amber), plenty of white and including black and grey in the writing. The final design should communicate collaboration, creativity and professionalism and that we are approachable.

Industry/Entity Type

Town

```html
<!DOCTYPE html>
<html lang="en">
<head>
<meta charset="utf-8">
<title>Fernhill Civic Studio — Business Card</title>
<link rel="stylesheet" href="https://fonts.googleapis.com/css2?family=Exo+2:wght@400;600&family=Oswald:wght@400;500&display=swap">
<style>
  :root {
    --paper: #ffffff;
    --stage: #eeeeec;
    --frame-grey: #cfd3d5;
    --ink: #111111;
    --ink-soft: #4a4a4a;
    --band-black: #0b0b0b;
    --brand-blue: #1e9cc6;
    --white: #ffffff;
  }
  * { box-sizing: border-box; margin: 0; padding: 0; }
  html, body { width: 1057px; height: 1200px; overflow: hidden; }
  body {
    background: var(--stage);
    font-family: "Exo 2", sans-serif;
    display: flex;
    align-items: center;
    justify-content: center;
    gap: 70px;
  }
  .card {
    width: 420px;
    height: 720px;
    background: var(--paper);
    position: relative;
    box-shadow: 0 6px 24px rgba(0,0,0,0.12);
  }
  .card--front { border: 14px solid var(--frame-grey); }
  .card--back {
    border: 16px solid var(--brand-blue);
    display: flex;
    align-items: center;
    justify-content: center;
    padding-bottom: 90px;
  }

  .brand { display: flex; flex-direction: column; align-items: center; gap: 8px; }
  .brand__dot { width: 74px; height: 74px; border-radius: 50%; background: var(--brand-blue); }
  .brand__name { font-family: "Exo 2", sans-serif; font-weight: 600; font-size: 19px; color: var(--ink-soft); white-space: nowrap; }
  .card--front .brand { position: absolute; top: 44px; right: 30px; }
  .card--back .brand__dot { width: 96px; height: 96px; }
  .card--back .brand__name { font-size: 26px; }

  .person { position: absolute; top: 200px; left: 30px; }
  .person__name { font-family: "Oswald", sans-serif; font-weight: 500; font-size: 30px; color: var(--ink); letter-spacing: 1px; line-height: 1.1; }
  .person__role { font-family: "Oswald", sans-serif; font-size: 13px; color: var(--ink-soft); letter-spacing: 2px; margin-top: 4px; }

  .contact-band {
    position: absolute; left: 0; right: 0; top: 290px; height: 250px;
    background: var(--band-black);
    padding: 34px 30px;
    display: flex; flex-direction: column; gap: 22px;
  }
  .contact-row { display: flex; align-items: center; gap: 14px; color: var(--white); font-size: 14px; letter-spacing: 0.5px; }
  .contact-row svg { width: 26px; height: 26px; flex: none; }

  .address-bar {
    position: absolute; left: 0; right: 0; top: 540px; height: 58px;
    background: var(--brand-blue);
    display: flex; align-items: center; gap: 12px; padding: 0 30px;
    color: var(--white); font-size: 13.5px; white-space: nowrap;
  }
  .address-bar svg { width: 26px; height: 26px; flex: none; }
</style>
</head>
<body>

<section class="card card--front" aria-label="Card front">
  <div class="brand">
    <span class="brand__dot"></span>
    <span class="brand__name">Fernhill Civic Studio</span>
  </div>

  <div class="person">
    <p class="person__name">DANIEL REYES</p>
    <p class="person__role">GENERAL MANAGER</p>
  </div>

  <div class="contact-band">
    <p class="contact-row">
      <svg viewBox="0 0 26 26" aria-hidden="true"><rect width="26" height="26" rx="3" fill="#fff"/><path d="M8 6.5l3 .4 1 3.2-1.7 1.2a9 9 0 0 0 4.4 4.4l1.2-1.7 3.2 1 .4 3c-6.5 1-12.5-5-11.5-11.5z" fill="#0b0b0b"/></svg>
      012 555 0147
    </p>
    <p class="contact-row">
      <svg viewBox="0 0 26 26" aria-hidden="true"><rect width="26" height="26" rx="3" fill="#fff"/><rect x="9" y="5" width="8" height="16" rx="1.5" fill="none" stroke="#0b0b0b" stroke-width="1.8"/><circle cx="13" cy="18.3" r="1" fill="#0b0b0b"/></svg>
      012 555 0148
    </p>
    <p class="contact-row">
      <svg viewBox="0 0 26 26" aria-hidden="true"><rect width="26" height="26" rx="3" fill="#fff"/><rect x="6" y="8" width="14" height="10" fill="none" stroke="#0b0b0b" stroke-width="1.8"/><path d="M6 8l7 6 7-6" fill="none" stroke="#0b0b0b" stroke-width="1.8"/></svg>
      hello@fernhillcivic.com
    </p>
    <p class="contact-row">
      <svg viewBox="0 0 26 26" aria-hidden="true"><rect width="26" height="26" rx="3" fill="#fff"/><circle cx="13" cy="13" r="7" fill="none" stroke="#0b0b0b" stroke-width="1.6"/><ellipse cx="13" cy="13" rx="3" ry="7" fill="none" stroke="#0b0b0b" stroke-width="1.4"/><path d="M6 13h14" stroke="#0b0b0b" stroke-width="1.4"/></svg>
      www.fernhillcivic.com
    </p>
  </div>

  <div class="address-bar">
    <svg viewBox="0 0 26 26" aria-hidden="true"><rect width="26" height="26" rx="3" fill="#fff"/><path d="M13 5a5.5 5.5 0 0 0-5.5 5.5C7.5 15 13 21 13 21s5.5-6 5.5-10.5A5.5 5.5 0 0 0 13 5z" fill="#1e9cc6"/><circle cx="13" cy="10.5" r="2" fill="#fff"/></svg>
    42 Meridian Lane, Level 3, Harbour St
  </div>
</section>

<section class="card card--back" aria-label="Card back">
  <div class="brand">
    <span class="brand__dot"></span>
    <span class="brand__name">Fernhill Civic Studio</span>
  </div>
</section>

</body>
</html>
```